Business Card for a Jewellery Brand

Business card for an upscale jewellery brand. Attached is the brand logo and icon and color board. I am looking for two card versions: one for the founder and one is generic. The card should be elegant and convey upscale and premium feel. I am open to both square and rectangle card shapes.

Industry/Entity Type

Jewelry

Contact Information for Business Card

Two cards: (1) Sunela Parvaniya (Founder) (2) General
(1) Sunela Parvaniya card should have Name: Sunela Parvaniya, Title: Founder Email id: sunela@quiremo.com.au. Phone no: +61452913307
(2) Generic card should have Email id: info@quiremo.com.au. Phone no: +61436207518

Requirements
Must have
• Workmark
• ICON
• Phone no
• Email ID
• ABN: 58219740312 (Note: ABN is Business number in Australia)
• Website: www.quiremo.com.au
• Instagram: quiremo_jewellery
• Facebook: @quiremojewellery
Nice to have
• Tagline

```html
<!DOCTYPE html>
<html lang="en">
<head>
<meta charset="UTF-8">
<title>Quiremo Business Cards</title>
<link rel="stylesheet" href="https://fonts.googleapis.com/css2?family=Open+Sans:wght@300;400;700&display=swap">
<style>
  :root {
    --page: #2b2624;
    --card: #121315;
    --rose: #c98c88;
    --white: #f2f2f2;
    --grey: #9a9a9a;
    --rule: #bdbdbd;
  }
  * { box-sizing: border-box; margin: 0; padding: 0; }
  html, body { width: 1200px; height: 864px; overflow: hidden; }
  body {
    background: var(--page);
    font-family: "Open Sans", Arial, sans-serif;
    display: flex;
    flex-direction: column;
    align-items: center;
    justify-content: center;
    gap: 30px;
  }
  .card {
    position: relative;
    width: 680px;
    height: 388px;
    background: var(--card);
    box-shadow: 0 10px 30px rgba(0,0,0,.45);
    overflow: hidden;
  }
  .brand { display: flex; flex-direction: column; align-items: center; }
  .brand-mark { border-radius: 50%; border: 2px solid var(--rose); }
  .brand-name {
    color: var(--rose);
    font-weight: 300;
    line-height: 1;
  }

  /* front */
  .front .brand {
    position: absolute;
    left: 0; right: 0; top: 82px;
    gap: 18px;
  }
  .front .brand-mark { width: 54px; height: 54px; }
  .front .brand-name { font-size: 46px; letter-spacing: 16px; padding-left: 16px; }
  .tagline-row {
    position: absolute;
    left: 20px; right: 20px; top: 262px;
    display: flex; align-items: center; gap: 10px;
  }
  .tagline-row .rule { flex: 1; height: 1px; background: var(--rule); }
  .tagline-row .rule.left { flex: 0 0 210px; }
  .tagline { color: var(--grey); font-size: 12px; letter-spacing: 1px; white-space: nowrap; }

  /* back */
  .person { position: absolute; left: 36px; top: 150px; }
  .person-name { color: var(--rose); font-weight: 700; font-size: 16px; line-height: 22px; }
  .person-title { color: var(--white); font-size: 16px; line-height: 22px; }
  .divider {
    position: absolute;
    left: 104px; right: 36px; top: 210px;
    height: 1px; background: var(--rule);
  }
  .contacts { position: absolute; left: 36px; top: 222px; list-style: none; }
  .contacts li {
    display: flex; align-items: center; gap: 10px;
    color: var(--white); font-size: 15px; line-height: 22px;
  }
  .contacts .icon { width: 12px; height: 12px; flex: none; }
  .social-box { width: 11px; height: 11px; background: var(--rose); flex: none; border-radius: 2px; }
  .back .brand { position: absolute; right: 52px; top: 64px; gap: 14px; }
  .back .brand-mark { width: 48px; height: 48px; }
  .back .brand-name { font-size: 40px; letter-spacing: 14px; padding-left: 14px; }
  .business-info {
    position: absolute; right: 40px; top: 262px;
    color: var(--white); font-size: 15px; line-height: 24px;
  }
</style>
</head>
<body>
  <section class="card front" aria-label="Card front">
    <div class="brand">
      <span class="brand-mark"></span>
      <span class="brand-name">QUIREMO</span>
    </div>
    <div class="tagline-row">
      <span class="rule left"></span>
      <span class="tagline">LOVE IS IN THE AIR</span>
      <span class="rule"></span>
    </div>
  </section>

  <section class="card back" aria-label="Card back">
    <div class="brand">
      <span class="brand-mark"></span>
      <span class="brand-name">QUIREMO</span>
    </div>
    <div class="person">
      <p class="person-name">Sunela Parvaniya</p>
      <p class="person-title">Founder</p>
    </div>
    <span class="divider"></span>
    <ul class="contacts">
      <li>
        <svg class="icon" viewBox="0 0 12 12" aria-hidden="true"><rect x="3" y="0.5" width="6" height="11" rx="1.2" fill="none" stroke="#c98c88" stroke-width="1.2"/><circle cx="6" cy="9.5" r="0.7" fill="#c98c88"/></svg>
        +61452913307
      </li>
      <li>
        <svg class="icon" viewBox="0 0 12 12" aria-hidden="true"><rect x="0.5" y="2" width="11" height="8" fill="#c98c88"/><path d="M0.5 2 L6 6.5 L11.5 2" fill="none" stroke="#121315" stroke-width="1"/></svg>
        sunela@quiremo.com.au
      </li>
      <li><span class="social-box"></span>quiremo_jewellery</li>
      <li><span class="social-box"></span>@quiremojewellery</li>
    </ul>
    <div class="business-info">
      <p>ABN: 58219740312</p>
      <p>www.quiremo.com.au</p>
    </div>
  </section>
</body>
</html>
```